KRWB new business card design

We need a business card design for our established business which is Australia wide however based in Melbourne. We are a young team of Financial Planners who specialize in Insurance and Basic super advice for people like us.

We are people who help our clients get things done in a timely and cost effective manner whilst having a good time and a laugh along the way.

We would like this to have a consistent feel with our new e-brochure which i have attached from a color and font perspective.

Industry/Entity Type

Business

Requirements
Must have
• We do not need specific address details rather just the states we are in:

VIC/NSW/QLD/TAS
Nice to have
• Curved edge to mate the brochure

```html
<!DOCTYPE html>
<html lang="en">
<head>
<meta charset="utf-8">
<title>KRWB business card concepts</title>
<link href="https://fonts.googleapis.com/css2?family=Questrial&family=Arimo:wght@400;700&display=swap" rel="stylesheet">
<style>
  :root {
    --bg: #e9e6e1;
    --card: #0b0b0b;
    --green-dark: #1fa447;
    --green-light: #8cc63f;
    --white: #ffffff;
    --grey: #d9d9d9;
  }
  * { box-sizing: border-box; margin: 0; padding: 0; }
  html, body { width: 1200px; height: 502px; overflow: hidden; background: var(--bg); }
  .sheet { position: relative; width: 1200px; height: 502px; }
  .card {
    position: absolute; width: 353px; height: 203px; background: var(--card);
    color: var(--white); font-family: "Questrial", sans-serif; overflow: hidden;
  }
  .brand {
    display: flex; align-items: center; justify-content: center; gap: 6px;
    font-family: "Questrial", sans-serif; color: var(--green-light); letter-spacing: 1px;
  }
  .brand .mark { width: 12px; height: 12px; background: var(--green-dark); }
  .brand.white { color: var(--white); }
  .brand.white .mark { background: var(--white); }
  .heading { font-weight: 700; letter-spacing: 2.5px; font-size: 13px; font-family: "Arimo", sans-serif; }
  .services { list-style: none; }
  .services li::before { content: "•"; color: var(--green-light); margin-right: 4px; }
  .photo {
    position: absolute; top: 0; right: 0; bottom: 0; width: 56px;
    border-left: 4px solid var(--green-light); border-bottom-left-radius: 46px;
    background: linear-gradient(180deg, #bdbdbd, #6e6e6e 60%, #2a2a2a);
  }

  /* card 1 – adviser front */
  .card-adviser { left: 36px; top: 30px; }
  .card-adviser .body { position: absolute; left: 0; top: 6px; width: 297px; text-align: center; font-family: "Arimo", sans-serif; }
  .card-adviser .name { font-size: 12.5px; font-weight: 700; }
  .card-adviser .name em { font-weight: 400; font-size: 10.5px; }
  .card-adviser .role { font-size: 11px; margin-top: 1px; }
  .card-adviser .brand { font-size: 34px; margin: 14px 0 14px; }
  .card-adviser .contact { font-size: 8.6px; line-height: 1.55; }
  .card-adviser .legal { font-size: 7.3px; line-height: 1.15; margin-top: 6px; }

  /* card 2 – team photo */
  .card-team { left: 425px; top: 28px; }
  .card-team .body { position: absolute; left: 0; top: 14px; width: 297px; text-align: center; }
  .card-team .brand { font-size: 44px; margin-bottom: 22px; }
  .card-team .services { font-size: 11.5px; line-height: 1.6; }
  .card-team .services li { display: inline; margin: 0 3px; }

  /* card 3 – columns */
  .card-columns { left: 815px; top: 31px; border-bottom-right-radius: 30px; }
  .card-columns .brand { font-size: 48px; margin-top: 28px; }
  .card-columns .heading { text-align: center; margin-top: 28px; }
  .card-columns .cols { display: flex; justify-content: center; align-items: flex-end; margin-top: 12px; font-size: 10.5px; line-height: 1.4; }
  .card-columns .cols ul { padding: 0 6px; border-right: 1px solid var(--green-dark); }
  .card-columns .cols ul:last-child { border-right: 0; }

  /* card 4 – mono */
  .card-mono { left: 38px; top: 274px; border-bottom-right-radius: 30px; text-align: center; }
  .card-mono .brand { font-size: 46px; margin-top: 34px; }
  .card-mono .heading { margin-top: 36px; }
  .card-mono .services { font-size: 11.5px; line-height: 1.6; margin-top: 4px; }
  .card-mono .services li { display: inline; margin: 0 2px; }
  .card-mono .web { font-size: 11px; letter-spacing: 2.5px; margin-top: 2px; }

  /* card 5 – split */
  .card-split { left: 432px; top: 274px; border-bottom-right-radius: 32px; }
  .card-split .edge { position: absolute; top: 0; right: 0; bottom: 0; width: 5px; background: var(--green-light); border-bottom-right-radius: 32px; }
  .card-split .brand { position: absolute; left: 20px; top: 84px; font-size: 38px; }
  .card-split .divider { position: absolute; left: 174px; top: 44px; width: 1px; height: 110px; background: linear-gradient(180deg, transparent, var(--white), transparent); }
  .card-split .list { position: absolute; left: 190px; top: 38px; }
  .card-split .services { font-size: 11.5px; line-height: 1.85; margin-top: 10px; }

  /* card 6 – list left */
  .card-list { left: 818px; top: 278px; border-top-left-radius: 30px; }
  .card-list .list { position: absolute; left: 26px; top: 26px; }
  .card-list .heading { font-size: 14px; }
  .card-list .services { font-size: 14px; line-height: 1.8; margin-top: 6px; }
  .card-list .brand { position: absolute; left: 236px; top: 90px; font-size: 32px; }
</style>
</head>
<body>
<main class="sheet">

  <article class="card card-adviser">
    <div class="body">
      <p class="name">Daniel Hartley <em>ADFS, BBus, LRS©</em></p>
      <p class="role">Financial Adviser</p>
      <div class="brand"><span class="mark"></span>KRWB</div>
      <p class="contact">✆ 1300 555 014 &nbsp; ▯ 0400 555 218 &nbsp; ☎ 03 9555 0147</p>
      <p class="contact">✉ daniel@krwb.com.au &nbsp; States: VIC/NSW/QLD/TAS</p>
      <p class="legal">KRWB Pty Ltd<br>Authorised Representatives, Meridale Financial Planning Limited<br>Australian Financial Services Licensee</p>
    </div>
    <div class="photo" role="img" aria-label="Black and white portrait of the adviser"></div>
  </article>

  <article class="card card-team">
    <div class="body">
      <div class="brand"><span class="mark"></span>KRWB</div>
      <p class="heading">Specialising in:</p>
      <ul class="services">
        <li>Risk Insurance</li><li>Debt Management</li><br><li>Superannuation</li><br><li>Wealth Creation</li><li>Retirement Planning</li>
      </ul>
    </div>
    <div class="photo" role="img" aria-label="Portrait of a smiling team member"></div>
  </article>

  <article class="card card-columns">
    <div class="brand"><span class="mark"></span>KRWB</div>
    <p class="heading">Specialising in:</p>
    <div class="cols">
      <ul class="services"><li>Risk Insurance</li><li>Debt Management</li></ul>
      <ul class="services"><li>Superannuation</li><li>Wealth Creation</li></ul>
      <ul class="services"><li>Retirement Planning</li></ul>
    </div>
  </article>

  <article class="card card-mono">
    <div class="brand white"><span class="mark"></span>KRWB</div>
    <p class="heading">Specialising in:</p>
    <ul class="services">
      <li>Risk Insurance</li><li>Debt Management</li><li>Superannuation</li><br><li>Wealth Creation</li><li>Retirement Planning</li>
    </ul>
    <p class="web">www.krwb.com.au</p>
  </article>

  <article class="card card-split">
    <div class="brand"><span class="mark"></span>KRWB</div>
    <div class="divider"></div>
    <div class="list">
      <p class="heading">Specialising in:</p>
      <ul class="services"><li>Risk Insurance</li><li>Debt Management</li><li>Superannuation</li><li>Wealth Creation</li><li>Retirement Planning</li></ul>
    </div>
    <div class="edge"></div>
  </article>

  <article class="card card-list">
    <div class="list">
      <p class="heading">Specialising in:</p>
      <ul class="services"><li>Risk Insurance</li><li>Debt Management</li><li>Superannuation</li><li>Wealth Creation</li><li>Retirement Planning</li></ul>
    </div>
    <div class="brand"><span class="mark"></span>KRWB</div>
  </article>

</main>
</body>
</html>
```